Business Cards for IT Consulting Company (Managed Service Provider)

I am looking to have some business cards printed and would like some designs. We are an IT Consulting company based in Vancouver BC. I would like a nice clean and modern look to the cards. I have uploaded all the versions of my logo so parts can be used as needed. Here is a snippit from our website homepage:

Quillbrook Networks Ltd. is an IT Solutions Partner located in Vancouver BC, Canada. We offer IT solutions and support to customers in the greater Vancouver Area. With expertise in Microsoft platforms, as well as Linux and Mac OSX and over 12 years experience in the IT industry, Quillbrook Networks is dedicated to offering our clients top quality service and products. We take pride in the solutions we offer our customers. The greatest compliment a client can give us is to recommend our services.

Quillbrook Networks Ltd. offers a wide range of IT services from onsite service to remote support and managed service solutions. This allows clients to choose the support path that best suits their company’s needs. Supporting many different sized companies from small to enterprise level over the past 12 years Quillbrook Networks has the experience and expertise needed to ensure things run smoothly. Allowing our clients to focus on doing business.

Revolutionizing the way IT services are delivered.

Quillbrook Networks is dedicated to providing our clients with IT solutions that work and grow with them for years to come. This philosophy helps save money in the long run instead of replacing equipment constantly. Far too often IT solutions are not well thought out and while possibly solving the problem at hand, require replacement due to growth or quality within a very short time frame. Quillbrook Networks takes pride in providing solutions that will last and be able to accommodate growth without the need for replacement.

Industry/Entity Type

Information Technology

Contact Information for Business Card

Quillbrook Networks Ltd.
(Employee Name)
Eml: (Employees Email Address)
Web: quillbrook.me
Ph: 604-555-0148

Font styles to use
Serif
Sans Serif

Requirements
Must have
• The Company logo and company colors.
Nice to have
• - Our tag line: "Revolutionizing IT Services" or "Revolutionizing the way IT services are delivered."
• - Also I really like the idea of nature and technology together blending which is sort of where my logo came from so integrating that somehow onto the business cards would be great.

```html
<!DOCTYPE html>
<html lang="en">
<head>
<meta charset="utf-8">
<title>Quillbrook Networks Ltd. — Business Cards</title>
<link rel="stylesheet" href="https://fonts.googleapis.com/css2?family=Open+Sans:wght@400;600;700&display=swap">
<style>
  :root {
    --brand-blue: #00aeef;
    --paper: #ffffff;
    --paper-shade: #f1f1f1;
    --rule-grey: #6b6b6b;
    --backdrop: #e9e6e1;
    --ink-white: #ffffff;
  }
  * { box-sizing: border-box; margin: 0; padding: 0; }
  html, body {
    width: 1200px; height: 900px; overflow: hidden;
    background: var(--backdrop);
    font-family: "Open Sans", Arial, sans-serif;
  }
  .sheet {
    position: relative; width: 1200px; height: 900px;
    display: flex; align-items: center; justify-content: center; gap: 50px;
  }
  .card {
    position: relative; width: 525px; height: 300px; overflow: hidden;
    box-shadow: 0 6px 18px rgba(0,0,0,0.18);
  }

  /* Front */
  .card--front { background: var(--brand-blue); }
  .card--front .wordmark { position: absolute; top: 98px; left: 0; right: 0; justify-content: center; }
  .card--front .wordmark__name { color: var(--ink-white); }
  .card--front .wordmark__dot { background: var(--ink-white); }
  .tagline-band {
    position: absolute; left: 0; right: 0; top: 200px; height: 58px;
    background: var(--paper);
    display: flex; align-items: flex-end; justify-content: center; padding-bottom: 8px;
  }
  .tagline {
    color: var(--brand-blue); font-weight: 700; font-size: 17px; letter-spacing: 0.2px;
  }

  /* Back */
  .card--back { background: var(--brand-blue); }
  .card--back .top-panel {
    position: absolute; left: 0; right: 0; top: 0; height: 132px;
    background: linear-gradient(180deg, var(--paper) 0%, var(--paper-shade) 100%);
  }
  .card--back .divider {
    position: absolute; left: 0; right: 0; top: 132px; height: 14px;
    background: var(--paper);
    border-top: 5px solid var(--rule-grey);
  }
  .card--back .wordmark { position: absolute; top: 46px; left: 0; right: 0; justify-content: center; }
  .card--back .wordmark__name { color: var(--brand-blue); }
  .card--back .wordmark__dot { background: var(--brand-blue); }

  .wordmark { display: flex; align-items: center; gap: 14px; }
  .wordmark__dot { width: 34px; height: 34px; border-radius: 50%; }
  .wordmark__name { font-weight: 700; font-size: 30px; line-height: 1; letter-spacing: 0.3px; }

  .contact {
    position: absolute; top: 192px; left: 120px;
    display: flex; flex-direction: column; align-items: flex-end; gap: 6px;
    color: var(--ink-white); font-size: 14px;
  }
  .contact__row { display: flex; align-items: center; gap: 8px; }
  .contact__icon { width: 13px; height: 13px; fill: var(--ink-white); }
  .holder-name {
    position: absolute; top: 186px; left: 345px;
    color: var(--ink-white); font-weight: 700; font-size: 18px;
  }
</style>
</head>
<body>
<main class="sheet">

  <section class="card card--front" aria-label="Card front">
    <div class="wordmark">
      <span class="wordmark__dot"></span>
      <span class="wordmark__name">Quillbrook Networks Ltd.</span>
    </div>
    <div class="tagline-band">
      <p class="tagline">Revolutionizing IT Services</p>
    </div>
  </section>

  <section class="card card--back" aria-label="Card back">
    <div class="top-panel"></div>
    <div class="divider"></div>
    <div class="wordmark">
      <span class="wordmark__dot"></span>
      <span class="wordmark__name">Quillbrook Networks Ltd.</span>
    </div>

    <div class="contact">
      <div class="contact__row">
        <span>604-555-0148</span>
        <svg class="contact__icon" viewBox="0 0 16 16" aria-hidden="true"><path d="M3.6 1.2l2.3 2.3c.4.4.4 1 0 1.4L4.7 6.1c.9 2 2.6 3.7 4.6 4.6l1.2-1.2c.4-.4 1-.4 1.4 0l2.3 2.3c.4.4.4 1 0 1.4l-1.3 1.3c-.6.6-1.5.8-2.3.5C6 13.5 2.5 10 1 5.4c-.3-.8-.1-1.7.5-2.3l1.3-1.3c.3-.4.5-.6.8-.6z"/></svg>
      </div>
      <div class="contact__row">
        <span>info@quillbrook.me</span>
        <svg class="contact__icon" viewBox="0 0 16 16" aria-hidden="true"><path d="M1 3h14v10H1z M2 4.2v.4l6 4.2 6-4.2v-.4z" fill-rule="evenodd"/></svg>
      </div>
      <div class="contact__row">
        <span>www.quillbrook.me</span>
        <svg class="contact__icon" viewBox="0 0 16 16" aria-hidden="true"><circle cx="8" cy="8" r="7"/></svg>
      </div>
    </div>
    <p class="holder-name">Daniel Harper</p>
  </section>

</main>
</body>
</html>
```